Redesign of business card for Cedar Ridge Mechanical

We are looking for a new design for our business cards for Cedar Ridge Mechanical. We are a plumbing & HVAC construction company, operating on the West Coast of Canada and USA. Logo attached.
Industry/Entity Type
Construction - Plumbing & HVAC
Contact Information for Business Card
Name, address, phone numbers, email, website address
Look and feel
Each slider illustrates characteristics of the customer's brand and the style your logo design should communicate.

```html
<!DOCTYPE html>
<html lang="en">
<head>
<meta charset="utf-8">
<title>Cedar Ridge Mechanical – Business Card</title>
<link href="https://fonts.googleapis.com/css2?family=Oswald:wght@600&family=Roboto:wght@400;500&display=swap" rel="stylesheet">
<style>
  :root {
    --backdrop: #3a3a3a;
    --card-black: #0d0d0d;
    --card-white: #ffffff;
    --ink: #111111;
    --ink-soft: #333333;
    --rule: #9a9a9a;
  }
  * { margin: 0; padding: 0; box-sizing: border-box; }
  html, body { width: 1200px; height: 689px; overflow: hidden; }
  body {
    background: var(--backdrop);
    font-family: "Roboto", Arial, sans-serif;
    position: relative;
  }
  .card {
    position: absolute;
    top: 195px;
    width: 525px;
    height: 300px;
    border-radius: 22px;
    overflow: hidden;
    box-shadow: 0 18px 40px rgba(0,0,0,.45);
  }
  /* Back */
  .card--back {
    left: 45px;
    background: var(--card-black);
    display: flex;
    align-items: center;
    justify-content: center;
  }
  .back-pattern {
    position: absolute; inset: 0;
    background: linear-gradient(135deg, #1c1c1c 0%, #0a0a0a 60%, #141414 100%);
  }
  .back-name {
    position: relative;
    color: var(--card-white);
    font-family: "Roboto", Arial, sans-serif;
    font-weight: 500;
    font-size: 17px;
    letter-spacing: 2px;
    text-transform: uppercase;
  }
  /* Front */
  .card--front {
    left: 630px;
    background: var(--card-white);
  }
  .brand {
    position: absolute;
    left: 30px; top: 100px;
    width: 200px;
    display: flex; align-items: center; gap: 10px;
  }
  .brand-mark { width: 18px; height: 18px; background: var(--ink); flex: none; }
  .brand-name {
    font-weight: 500; font-size: 15px; line-height: 1.25;
    color: var(--ink); text-transform: uppercase; letter-spacing: .5px;
  }
  .divider {
    position: absolute; left: 238px; top: 40px;
    width: 1px; height: 170px;
    background: linear-gradient(to bottom, transparent, var(--rule) 20%, var(--rule) 80%, transparent);
  }
  .contact { position: absolute; left: 260px; top: 38px; color: var(--ink-soft); }
  .person-name {
    font-family: "Oswald", "Arial Narrow", sans-serif;
    font-weight: 600; font-size: 24px; color: var(--ink);
    line-height: 1; text-transform: uppercase;
  }
  .person-role { font-size: 13px; margin-bottom: 14px; }
  .contact-list { list-style: none; font-size: 13px; line-height: 1.5; }
  .contact-list li { display: flex; align-items: center; gap: 8px; }
  .contact-list svg { width: 11px; height: 11px; fill: var(--ink); flex: none; }
  .address { margin-top: 10px; font-size: 13px; line-height: 1.35; }
  .footer-rule {
    position: absolute; left: 0; right: 0; bottom: 46px;
    height: 2px; background: var(--ink);
  }
  .footer-band {
    position: absolute; left: 0; right: 0; bottom: 0;
    height: 38px; background: var(--card-black);
  }
</style>
</head>
<body>
  <section class="card card--back">
    <div class="back-pattern" role="img" aria-label="Dark repeating brand pattern background"></div>
    <span class="back-name">Cedar Ridge Mechanical</span>
  </section>

  <section class="card card--front">
    <div class="brand">
      <span class="brand-mark"></span>
      <span class="brand-name">Cedar Ridge Mechanical</span>
    </div>
    <div class="divider"></div>
    <div class="contact">
      <h1 class="person-name">Marcus Hale</h1>
      <p class="person-role">Managing Director</p>
      <ul class="contact-list">
        <li><svg viewBox="0 0 24 24"><path d="M6.6 10.8a15.1 15.1 0 0 0 6.6 6.6l2.2-2.2a1 1 0 0 1 1-.25 11.4 11.4 0 0 0 3.6.57 1 1 0 0 1 1 1V20a1 1 0 0 1-1 1A17 17 0 0 1 3 4a1 1 0 0 1 1-1h3.5a1 1 0 0 1 1 1c0 1.25.2 2.45.57 3.57a1 1 0 0 1-.25 1z"/></svg>044-987 654 321</li>
        <li><svg viewBox="0 0 24 24"><path d="M2 5h20v14H2z M2 5l10 8 10-8" /></svg>info@cedarridge.com</li>
        <li><svg viewBox="0 0 24 24"><circle cx="12" cy="12" r="10"/></svg>www.cedarridgemech.com</li>
      </ul>
      <p class="address">88, Harbour Road West<br>V6B 2K1, Canada</p>
    </div>
    <div class="footer-rule"></div>
    <div class="footer-band"></div>
  </section>
</body>
</html>
```